Maranoola Wines - web page for new Australian wine label

We need a landing page for our wine company. Maranoola is a family owned company, we grow the gapes, and make the wine in the Clare valley. Daniel Whitlock is the winemaker and is well known for his style, which is all about the fruit flavour rather than wood or age influences. Maranoola is Abriginal for 2 hills and a water source. We hand pick, hand plunge, foot crush resulting in elegant wine. Little to no additives, minimal filtering, single vineyard wines. Handcrafted with small releases of only the best fruit from carefully selected rows and bunches. The Clare valley is located two hours North of Adelaide, is known for cool climate and slow ripening, resulting in wines that have an elegant mouth feel, with bright colour and outstanding flavours. Our Brookmere vineyard has a Eastern aspect, gathering morning sun and escaping the hot afternoons, and in our opinion is on of the prettiest valleys in the world. Only 1000 cases per annum of the very best handpicked fruit, from the best rows. We hope you enjoy the Maranoola style, the reds are lighter in colour, fruit driven palate, more old world influence and the Riesling is on the dry side with fresh citrus. Minimal additives and filtering, our aim was to make wine with minimal influence from wine making. Handcrafted wines.

Target Market(s)

females 18 - 60 are the ones that buy 70 percent of wine, so whilst men are also a target, its the ladies we seek to appeal to.

Industry/Entity Type

It Company

Number of Pages Required

4 page

Font styles to use
Serif

Requirements
Must have
• Eye catching front page that makes me feel like i am ordering from quality company, that cares for what they do. Easy to use ordering, and delivery instructions.
• postage is $14.90 per case Australia wide.
• www.maranoolawines-example.com
Nice to have
• I want to see a fun and family oriented business that cares for the wine, we dont make a lot, its buckets and feet. But its wine made wanting to be the best in the world, we dont cut corners on quality. Handcrafted
Should not have
• dont really have any thoughts here, looking for all ideas

```html
<!DOCTYPE html>
<html lang="en">
<head>
<meta charset="utf-8">
<title>Maranoola Wines</title>
<link href="https://fonts.googleapis.com/css2?family=Noto+Serif:wght@400;700&family=Open+Sans:wght@400;600&display=swap" rel="stylesheet">
<style>
:root{
  --ink:#222222;
  --muted:#777777;
  --light:#9a9a9a;
  --brand:#1f6fb8;
  --white:#ffffff;
  --dark:#2b2b2b;
  --footer:#2e2e2e;
  --footer-bottom:#242424;
  --footer-text:#b8b8b8;
  --rule:#cfcfcf;
}
*{margin:0;padding:0;box-sizing:border-box}
html,body{width:1200px;height:3015px;overflow:hidden;background:var(--white)}
body{position:relative;font-family:"Noto Serif",Georgia,serif;color:var(--ink)}
.abs{position:absolute}

/* header */
.site-header{position:absolute;left:0;top:0;width:1200px;height:92px;background:var(--white)}
.brand{position:absolute;left:66px;top:18px;display:flex;align-items:center;gap:12px}
.brand-dot{width:16px;height:16px;border-radius:50%;background:var(--brand)}
.brand-name{font-size:38px;color:var(--brand);font-weight:400;line-height:56px}
.main-nav{position:absolute;right:80px;top:38px;display:flex;gap:76px;font-size:14px;letter-spacing:.3px}
.main-nav a{color:var(--ink);text-decoration:none}

/* hero */
.hero{position:absolute;left:0;top:92px;width:1200px;height:553px;
  background:linear-gradient(100deg,#3b3a34 0%,#5a5248 35%,#7a6d5e 55%,#4e5a6a 80%,#2f3b4a 100%)}
.hero-shade{position:absolute;inset:0;background:rgba(0,0,0,.28)}
.hero-title{position:absolute;left:0;width:1200px;top:178px;text-align:center;color:var(--white);font-size:70px;font-weight:400;letter-spacing:1px}
.hero-sub{position:absolute;left:0;width:1200px;top:272px;text-align:center;color:var(--white);font-size:21px;letter-spacing:.5px}
.btn{position:absolute;border:2px solid var(--white);color:var(--white);font-size:14px;letter-spacing:1px;text-align:center;line-height:42px;height:46px;text-transform:uppercase}
.hero .btn{left:507px;top:324px;width:186px}
.dots{position:absolute;left:576px;top:526px;display:flex;gap:6px}
.dots span{width:7px;height:7px;border-radius:50%;background:rgba(255,255,255,.45)}
.dots span:first-child{background:var(--white)}

/* promo band */
.promo{position:absolute;left:0;top:645px;width:1200px;height:344px}
.promo-delivery{position:absolute;left:0;top:0;width:600px;height:344px;background:var(--dark);color:var(--white)}
.promo-feedback{position:absolute;left:600px;top:0;width:600px;height:344px;
  background:linear-gradient(90deg,#2f2f2c 0%,#55534c 45%,#7d7565 75%,#a69a7c 100%)}
.promo-feedback .shade{position:absolute;inset:0;background:rgba(0,0,0,.35)}
.promo h2{position:absolute;font-size:48px;font-weight:400;letter-spacing:1px;color:var(--white)}
.promo-delivery h2{left:72px;top:68px}
.promo-delivery p{position:absolute;left:76px;top:138px;font-size:29px}
.promo-delivery .btn{left:77px;top:202px;width:186px}
.promo-feedback h2{left:72px;top:74px}
.promo-feedback p{position:absolute;left:74px;top:148px;font-family:"Open Sans",Arial,sans-serif;font-size:26px;color:var(--white)}
.promo-feedback .btn{left:76px;top:202px;width:186px}

/* section titles */
.section-title{position:absolute;left:0;width:1200px;text-align:center;font-size:27px;font-weight:400;letter-spacing:.5px}
.section-rule{position:absolute;left:573px;width:54px;height:1px;background:var(--rule)}

/* products */
.product{position:absolute;top:1168px;width:238px}
.product-photo{width:238px;height:307px}
.product-name{margin-top:24px;text-align:center;font-size:16px;letter-spacing:.3px}

/* blog */
.post{position:absolute;top:1705px;width:487px}
.post-photo{width:487px;height:241px}
.post-title{margin-top:26px;font-size:18px;font-weight:400}
.post-body{margin-top:12px;font-family:"Open Sans",Arial,sans-serif;font-size:11.5px;line-height:26px;color:var(--muted)}
.post-meta{margin-top:10px;font-family:"Open Sans",Arial,sans-serif;font-size:12px;color:var(--light)}

/* how it works */
.how{position:absolute;left:0;top:2181px;width:1200px;height:464px;
  background:linear-gradient(135deg,#4a3a33 0%,#6b5344 30%,#5c4a3e 55%,#7a6250 80%,#4b3c36 100%)}
.how .shade{position:absolute;inset:0;background:rgba(40,25,25,.35)}
.how-title{position:absolute;left:0;width:1200px;top:138px;text-align:center;color:var(--white);font-size:50px;font-weight:400;letter-spacing:1px}
.how-sub{position:absolute;left:0;width:1200px;top:210px;text-align:center;color:var(--white);font-size:26px;letter-spacing:.5px}
.how .btn{left:507px;top:271px;width:186px}

/* footer */
.site-footer{position:absolute;left:0;top:2645px;width:1200px;height:318px;background:var(--footer);color:var(--footer-text);font-family:"Open Sans",Arial,sans-serif}
.footer-col{position:absolute;top:58px}
.footer-heading{font-family:"Noto Serif",Georgia,serif;font-size:14px;letter-spacing:.8px;color:var(--white);text-transform:uppercase;margin-bottom:20px}
.footer-links{list-style:none;font-size:12px;line-height:26px}
.footer-post{display:flex;gap:18px;margin-bottom:24px}
.date-box{width:34px;height:40px;background:#444;color:var(--white);text-align:center;font-size:10px;line-height:13px;padding-top:7px}
.date-box b{display:block;font-size:12px}
.footer-post-title{font-size:12px;color:var(--white);line-height:18px}
.footer-post-views{font-size:11px;color:var(--footer-text);line-height:20px}
.social{display:flex;gap:8px}
.social span{width:28px;height:28px;border:1px solid #5a5a5a;display:block}
.newsletter{margin-top:8px;width:226px;height:34px;border:1px solid #555;display:flex;align-items:center;justify-content:space-between;padding:0 12px;font-size:11px;color:#8a8a8a}
.footer-bottom{position:absolute;left:0;top:2963px;width:1200px;height:52px;background:var(--footer-bottom);font-family:"Open Sans",Arial,sans-serif;font-size:12px;color:#8a8a8a;text-align:center;line-height:52px}
.footer-bottom b{color:var(--white);font-weight:600}
</style>
</head>
<body>

<header class="site-header">
  <div class="brand"><span class="brand-dot"></span><span class="brand-name">Maranoola</span></div>
  <nav class="main-nav">
    <a href="#">HOME</a><a href="#">ABOUT US</a><a href="#">PRODUCTS</a><a href="#">BLOG</a><a href="#">GALLERY</a><a href="#">CONTACT US</a>
  </nav>
</header>

<section class="hero" role="img" aria-label="Hand holding a bottle of white wine in front of shelves of wine bottles in a shop">
  <div class="hero-shade"></div>
  <h1 class="hero-title">MARANOOLA WINES</h1>
  <p class="hero-sub">WE HAND PICK, HAND PLUNGE, FOOT CRUSH RESULTING IN ELEGANT WINE.</p>
  <a class="btn">Contact here!</a>
  <div class="dots"><span></span><span></span><span></span><span></span></div>
</section>

<section class="promo">
  <div class="promo-delivery">
    <h2>DELIVERY CHARGE</h2>
    <p>IS $14.90 PER CASE</p>
    <a class="btn">View details</a>
  </div>
  <div class="promo-feedback" role="img" aria-label="Winery worker driving a forklift in the cellar">
    <div class="shade"></div>
    <h2>CUSTOMER</h2>
    <p>SATISFACTION</p>
    <a class="btn">Feed backs</a>
  </div>
</section>

<h2 class="section-title" style="top:1052px">OUR PRODUCTS</h2>
<div class="section-rule" style="top:1115px"></div>

<div class="product" style="left:98px">
  <div class="product-photo" role="img" aria-label="White wine bottle beside a bowl of crayfish on a beach" style="background:linear-gradient(180deg,#9cc3de 0%,#d8e4ea 45%,#e9e4da 60%,#c85a3e 85%,#e1ddd6 100%)"></div>
  <p class="product-name">LOREM IPSUM IS SIMPLY</p>
</div>
<div class="product" style="left:354px">
  <div class="product-photo" role="img" aria-label="Red wine being poured into a glass" style="background:linear-gradient(180deg,#d9b99a 0%,#b9836b 30%,#5a1526 60%,#2a0c14 100%)"></div>
  <p class="product-name">LOREM IPSUM IS SIMPLY</p>
</div>
<div class="product" style="left:609px">
  <div class="product-photo" role="img" aria-label="Bottle and glass of red wine on a dark table" style="background:linear-gradient(180deg,#2a2624 0%,#3b322d 50%,#5a3f2c 80%,#2b1e16 100%)"></div>
  <p class="product-name">LOREM IPSUM IS SIMPLY</p>
</div>
<div class="product" style="left:864px">
  <div class="product-photo" role="img" aria-label="Wine bottles packed in a wooden gift crate with straw" style="background:linear-gradient(160deg,#3a3428 0%,#7d6a45 40%,#c9b98e 65%,#8a6b3e 100%)"></div>
  <p class="product-name">LOREM IPSUM IS SIMPLY</p>
</div>

<h2 class="section-title" style="top:1598px">FROM THE BLOG</h2>
<div class="section-rule" style="top:1650px"></div>

<article class="post" style="left:98px">
  <div class="post-photo" role="img" aria-label="Grape picker holding up a bunch of red grapes in the vineyard" style="background:linear-gradient(180deg,#b9c0c4 0%,#6f7d55 35%,#4e5e33 65%,#7a6a3c 100%)"></div>
  <h3 class="post-title">Es simplemente el texto de</h3>
  <p class="post-body">Es simplemente el texto de relleno de las imprentas y archivos de texto. Lorem Ipsum ha sido el texto de relleno estándar de las industrias desde el año 1500, cuando un impresor (N. del T. persona que se dedica...</p>
  <p class="post-meta">22 Comment</p>
</article>
<article class="post" style="left:615px">
  <div class="post-photo" role="img" aria-label="Two children foot crushing grapes in a tub" style="background:linear-gradient(180deg,#4a4644 0%,#7a6f66 40%,#8e3a3c 75%,#5a2a2c 100%)"></div>
  <h3 class="post-title">Es simplemente el texto de</h3>
  <p class="post-body">Es simplemente el texto de relleno de las imprentas y archivos de texto. Lorem Ipsum ha sido el texto de relleno estándar de las industrias desde el año 1500, cuando un impresor (N. del T. persona que se dedica...</p>
  <p class="post-meta">22 Comment</p>
</article>

<section class="how" role="img" aria-label="Bunches of dark grapes hanging among vine leaves">
  <div class="shade"></div>
  <h2 class="how-title">HOW IT WORKS</h2>
  <p class="how-sub">VIEW PHOTO GALLERY</p>
  <a class="btn">Click here</a>
</section>

<footer class="site-footer">
  <div class="footer-col" style="left:102px">
    <h4 class="footer-heading">Maranoola</h4>
    <ul class="footer-links"><li>About us</li><li>Products</li><li>Blog</li><li>Gallery</li><li>Press</li><li>Contact us</li></ul>
  </div>
  <div class="footer-col" style="left:342px">
    <h4 class="footer-heading">Help</h4>
    <ul class="footer-links"><li>Payment</li><li>Shipping &amp; Returns</li><li>Size Guide</li><li>Gift Card</li><li>Faqs</li></ul>
  </div>
  <div class="footer-col" style="left:563px">
    <h4 class="footer-heading">From the blog</h4>
    <div class="footer-post"><div class="date-box"><b>5</b>JUN</div><div><p class="footer-post-title">Es simplemente el texto de</p><p class="footer-post-views">1655 &nbsp; views</p></div></div>
    <div class="footer-post"><div class="date-box"><b>5</b>JUN</div><div><p class="footer-post-title">Es simplemente el texto de</p><p class="footer-post-views">1655 &nbsp; views</p></div></div>
    <div class="footer-post"><div class="date-box"><b>5</b>JUN</div><div><p class="footer-post-title">Es simplemente el texto de</p><p class="footer-post-views">1655 &nbsp; views</p></div></div>
  </div>
  <div class="footer-col" style="left:874px">
    <h4 class="footer-heading">Follow us</h4>
    <div class="social"><span></span><span></span><span></span><span></span><span></span><span></span></div>
    <h4 class="footer-heading" style="margin-top:42px">Newsletter</h4>
    <div class="newsletter"><span>Enter your email id</span>
      <svg width="8" height="12" viewBox="0 0 8 12"><path d="M1 1l5 5-5 5" fill="none" stroke="#8a8a8a" stroke-width="1.5"/></svg>
    </div>
  </div>
</footer>
<div class="footer-bottom">Copyright © 2017. <b>Maranoola</b>. All rights reserved</div>

</body>
</html>
```